Mobile App UI for Telecommunications/Hosting Company

We are about to convert our existing self-service Customer Portal into a mobile phone application and need an elegant and professional UI/UX design. Our company provides telecommunication (voice/mobile/data) and hosting services to medium-sized business. The primary purpose of the application is to view trouble tickets, alerts, orders, and performance charts. This application is available to customers only - not the general public.

Please provide a UI design suitable for display on iPhone/Android devices. The attached document includes a proposed screen flow. You are free to design your own screens to display the same information elegantly.
Updates

Please note that the design should be based on the wireframes in the Word document, not the screenshots.  The screenshots are just to show our existing web portal look & feel.

Also, just a few screens are required for initial submission (3 would be great).

Thanks,
Dermot.

Target Market(s)

IT Managers away from their desk and using a mobile phone application.
Adult males from technical background aged 30-50.
Customers of Brindlewood Telecom have access to this application (not the general public). This is a self-service portal for customers only.

Industry/Entity Type

Business

Colors
0592cd
33a6d7
85cae6
cadf82
fde08a

Requirements
Must have
• Please look at the screenshots from our current Customer Portal site (part of the project brief). The mobile app does not have to look the same, but should follow a similar style.

Please check out our company web site at www.brindlewoodtelecom.example (this site is not the customer portal and has a different look at feel) to understand what Brindlewood Telecom does.
Nice to have
• Sharing capabilities via email/SMS.
A nice background image to make it stand out
The colours selected below are a guide only as they are similar to the corporate colours
- The priority is something that works on a phone - a design extendable to tablets is a nice to have as our existing web site looks OK on a tablet..

```html
<!DOCTYPE html>
<html lang="en">
<head>
<meta charset="utf-8">
<title>Brindlewood Telecom – Account Menu</title>
<link rel="stylesheet" href="https://fonts.googleapis.com/css2?family=Open+Sans:wght@300;400&display=swap">
<style>
  :root {
    --bar-dark: #3b3b3b;
    --bar-darker: #2e2e2e;
    --accent-blue: #2a9fd6;
    --button-soft: #3f93c7;
    --button-strong: #1b89c6;
    --drawer-bg: #262626;
    --drawer-line: #3c3c3c;
    --drawer-text: #e6e6e6;
    --badge-bg: #555555;
    --page-light: #f1f1f1;
    --page-mid: #dcdcdc;
    --panel-row: #f6f6f6;
    --panel-line: #e2e2e2;
    --page-text: #555555;
    --arrow: #8a8370;
    --logo-text: #d0d0d0;
  }
  * { box-sizing: border-box; margin: 0; padding: 0; }
  html, body { width: 676px; height: 1200px; overflow: hidden; }
  body {
    position: relative;
    font-family: "Open Sans", Arial, sans-serif;
    background: linear-gradient(160deg, var(--page-light) 0%, #fafafa 45%, var(--page-mid) 100%);
  }

  /* Top bar */
  .top-bar {
    position: absolute; left: 0; top: 0; width: 676px; height: 91px;
    background: linear-gradient(180deg, var(--bar-dark), var(--bar-darker));
  }
  .top-bar .add-button { position: absolute; left: 30px; top: 26px; }
  .brand {
    position: absolute; left: 200px; top: 0; height: 91px;
    display: flex; align-items: center; gap: 12px;
  }
  .brand-name { font-weight: 400; font-size: 27px; color: var(--logo-text); letter-spacing: 0.5px; }
  .brand-dot { width: 40px; height: 40px; border-radius: 50%; background: var(--accent-blue); }
  .settings-button {
    position: absolute; left: 576px; top: 0; width: 100px; height: 91px;
    background: var(--accent-blue); display: flex; align-items: center; justify-content: center;
  }

  /* Page behind drawer */
  .page-title { position: absolute; left: 470px; top: 124px; font-size: 42px; font-weight: 300; color: #444; }
  .page-list {
    position: absolute; left: 470px; top: 206px; width: 174px; height: 472px;
    background: var(--panel-row); border: 1px solid var(--panel-line); border-radius: 4px;
    box-shadow: 0 1px 2px rgba(0,0,0,0.08);
  }
  .page-list-row { height: 94px; border-bottom: 1px solid var(--panel-line); position: relative; }
  .page-list-row:last-child { border-bottom: none; }
  .page-list-row.is-active { background: #ecebe8; }
  .page-list-row svg { position: absolute; left: 118px; top: 38px; }
  .subscribe-button {
    position: absolute; left: 470px; top: 714px; width: 174px; height: 78px;
    background: linear-gradient(180deg, #fbfbfb, #ececec); border: 1px solid #cfcfcf; border-radius: 3px;
    font-size: 20px; color: var(--page-text); display: flex; align-items: center; justify-content: flex-end; padding-right: 53px;
  }
  .page-note {
    position: absolute; right: 42px; top: 820px; text-align: right;
    font-size: 20px; line-height: 26px; color: var(--page-text);
  }

  /* Drawer */
  .side-drawer {
    position: absolute; left: 0; top: 91px; width: 486px; height: 876px;
    background: radial-gradient(ellipse at 80% 40%, #333 0%, var(--drawer-bg) 60%, #1f1f1f 100%);
  }
  .profile { position: absolute; left: 44px; top: 36px; display: flex; align-items: center; }
  .profile-photo {
    width: 92px; height: 92px; border-radius: 50%;
    background: radial-gradient(circle at 50% 40%, #b59a82, #6f8aa0 70%);
    border: 4px solid #6f6f6f;
  }
  .profile-name { margin-left: 30px; font-size: 35px; font-weight: 300; color: var(--drawer-text); }
  .menu { position: absolute; left: 0; top: 140px; width: 486px; list-style: none; }
  .menu-item {
    height: 64px; border-bottom: 1px solid var(--drawer-line);
    display: flex; align-items: center; justify-content: space-between;
    padding: 0 20px 0 46px; font-size: 25px; font-weight: 300; color: var(--drawer-text);
  }
  .menu-item:first-child { height: 64px; }
  .menu-item:last-child { border-bottom: none; }
  .menu-badge {
    min-width: 38px; height: 32px; border-radius: 4px; background: var(--badge-bg);
    font-size: 22px; font-weight: 400; color: #f0f0f0; display: flex; align-items: center; justify-content: center;
  }
  .drawer-button {
    position: absolute; left: 54px; width: 377px; height: 68px; border-radius: 3px;
    display: flex; align-items: center; justify-content: center;
    font-size: 27px; font-weight: 300; color: #eaf5fb;
  }
  .drawer-button.edit-profile { top: 652px; background: var(--button-soft); }
  .drawer-button.sign-out { top: 743px; background: var(--button-strong); }
</style>
</head>
<body>

  <div class="page-title">e</div>
  <div class="page-list">
    <div class="page-list-row"><svg width="14" height="16"><polygon points="0,0 14,8 0,16" fill="#8a8370"/></svg></div>
    <div class="page-list-row"><svg width="14" height="16"><polygon points="0,0 14,8 0,16" fill="#8a8370"/></svg></div>
    <div class="page-list-row"><svg width="14" height="16"><polygon points="0,0 14,8 0,16" fill="#8a8370"/></svg></div>
    <div class="page-list-row is-active"><svg width="14" height="16"><polygon points="0,0 14,8 0,16" fill="#8a8370"/></svg></div>
    <div class="page-list-row"><svg width="14" height="16"><polygon points="0,0 14,8 0,16" fill="#8a8370"/></svg></div>
  </div>
  <div class="subscribe-button">Subscribe</div>
  <div class="page-note">th empty head.<br>can go thru too.</div>

  <header class="top-bar">
    <svg class="add-button" width="38" height="38" viewBox="0 0 38 38" aria-label="Add">
      <rect x="17" y="2" width="4" height="34" fill="#fff"/>
      <rect x="2" y="17" width="34" height="4" fill="#fff"/>
    </svg>
    <div class="brand">
      <span class="brand-name">Brindlewood Telecom</span>
      <span class="brand-dot"></span>
    </div>
    <div class="settings-button" aria-label="Settings">
      <svg width="42" height="42" viewBox="0 0 42 42">
        <g fill="#fff" transform="translate(21 21)">
          <rect x="-4" y="-20" width="8" height="10" rx="1"/>
          <rect x="-4" y="-20" width="8" height="10" rx="1" transform="rotate(45)"/>
          <rect x="-4" y="-20" width="8" height="10" rx="1" transform="rotate(90)"/>
          <rect x="-4" y="-20" width="8" height="10" rx="1" transform="rotate(135)"/>
          <rect x="-4" y="-20" width="8" height="10" rx="1" transform="rotate(180)"/>
          <rect x="-4" y="-20" width="8" height="10" rx="1" transform="rotate(225)"/>
          <rect x="-4" y="-20" width="8" height="10" rx="1" transform="rotate(270)"/>
          <rect x="-4" y="-20" width="8" height="10" rx="1" transform="rotate(315)"/>
          <circle r="14"/>
        </g>
        <circle cx="21" cy="21" r="6" fill="#2a9fd6"/>
      </svg>
    </div>
  </header>

  <nav class="side-drawer">
    <div class="profile">
      <div class="profile-photo" role="img" aria-label="User profile photo"></div>
      <span class="profile-name">Anika Verhoeven</span>
    </div>
    <ul class="menu">
      <li class="menu-item">Events</li>
      <li class="menu-item">Biling <span class="menu-badge">10</span></li>
      <li class="menu-item">Orders <span class="menu-badge">2</span></li>
      <li class="menu-item">Tickets <span class="menu-badge">5</span></li>
      <li class="menu-item">Self Service <span class="menu-badge">5</span></li>
      <li class="menu-item">Help</li>
    </ul>
    <div class="drawer-button edit-profile">Edit my profile</div>
    <div class="drawer-button sign-out">Signout me!</div>
  </nav>

</body>
</html>
```